MRT Property - Business Cards

Looking for a business card & general letterhead, signage etc design for our new logo.

Colours:
000a20
0056a2
00b5ef
0088ce
68cef2

Fonts:
Poppins
Karla

Please keep look and feel of new brand - example in the zip package I sent.

```html
<!DOCTYPE html>
<html lang="en">
<head>
<meta charset="utf-8">
<title>MRT Property – Business Cards</title>
<link rel="stylesheet" href="https://fonts.googleapis.com/css2?family=Poppins:wght@400;500;700;800&display=swap">
<style>
  :root {
    --stage: #232323;
    --card: #0b1120;
    --navy: #000a20;
    --brand-blue: #0056a2;
    --cyan: #00b5ef;
    --mid-blue: #0088ce;
    --light-blue: #68cef2;
    --text: #f2f5fa;
  }
  * { box-sizing: border-box; margin: 0; padding: 0; }
  html, body { width: 1200px; height: 781px; overflow: hidden; }
  body {
    background: var(--stage);
    font-family: "Poppins", sans-serif;
    position: relative;
  }
  .card {
    position: absolute;
    top: 236px;
    width: 540px;
    height: 309px;
    border-radius: 26px;
    background: var(--card);
    box-shadow: 0 4px 0 var(--cyan), 0 18px 30px rgba(0,0,0,.45);
    overflow: hidden;
  }
  .card--front { left: 36px; }
  .card--back { left: 624px; }

  .brand-area {
    position: absolute;
    left: 60px;
    top: 30px;
    width: 300px;
    height: 250px;
    border-radius: 50% 40% 50% 50%;
    background: radial-gradient(ellipse at 30% 50%, #5c5f6e 0%, #2a2e3d 45%, rgba(11,17,32,0) 75%);
  }

  .identity {
    position: absolute;
    left: 34px;
    top: 134px;
    display: flex;
    align-items: center;
    gap: 10px;
  }
  .identity__dot {
    width: 22px; height: 22px;
    border-radius: 50%;
    background: var(--mid-blue);
  }
  .identity__name {
    font-weight: 700;
    font-size: 25px;
    color: var(--brand-blue);
    letter-spacing: .2px;
  }
  .divider {
    position: absolute;
    left: 256px;
    top: 58px;
    width: 1.5px;
    height: 196px;
    background: var(--mid-blue);
  }
  .details {
    position: absolute;
    left: 278px;
    top: 66px;
    color: var(--text);
    font-size: 13px;
    line-height: 1.4;
  }
  .details__name {
    font-weight: 800;
    font-size: 19px;
    color: var(--brand-blue);
    text-transform: uppercase;
    line-height: 1.1;
  }
  .details__role { font-size: 13.5px; margin-bottom: 12px; }
  .details__address { margin-bottom: 12px; }
  .contact { list-style: none; }
  .contact li { display: flex; align-items: center; gap: 7px; }
  .contact svg { width: 12px; height: 12px; flex: none; }
</style>
</head>
<body>
  <section class="card card--front" aria-label="Card front">
    <div class="brand-area" role="img" aria-label="Large brand mark decoration"></div>
  </section>

  <section class="card card--back" aria-label="Card back">
    <div class="identity">
      <span class="identity__dot"></span>
      <span class="identity__name">MRT Property</span>
    </div>
    <div class="divider"></div>
    <div class="details">
      <p class="details__name">Daniel Reed</p>
      <p class="details__role">Managing Director</p>
      <p class="details__address">Your address, City<br>State, Zip 1234</p>
      <ul class="contact">
        <li>
          <svg viewBox="0 0 24 24" aria-hidden="true"><path fill="#00b5ef" d="M6.6 10.8a15.1 15.1 0 0 0 6.6 6.6l2.2-2.2c.3-.3.7-.4 1-.2 1.1.4 2.3.6 3.6.6.6 0 1 .4 1 1V20c0 .6-.4 1-1 1A17 17 0 0 1 3 4c0-.6.4-1 1-1h3.5c.6 0 1 .4 1 1 0 1.3.2 2.5.6 3.6.1.3 0 .7-.2 1z"/></svg>
          123 456 789
        </li>
        <li>
          <svg viewBox="0 0 24 24" aria-hidden="true"><rect x="2" y="5" width="20" height="14" rx="2" fill="#00b5ef"/><path d="M3 6l9 7 9-7" fill="none" stroke="#0b1120" stroke-width="2"/></svg>
          info@yourmail.com
        </li>
        <li>
          <svg viewBox="0 0 24 24" aria-hidden="true"><circle cx="12" cy="12" r="10" fill="none" stroke="#00b5ef" stroke-width="2"/><path d="M2 12h20M12 2c3 3 3 17 0 20M12 2c-3 3-3 17 0 20" fill="none" stroke="#00b5ef" stroke-width="1.6"/></svg>
          www.yourwebsite.com
        </li>
      </ul>
    </div>
  </section>
</body>
</html>
```